Silver Bloom Marisol's Cleaning Service Business Cards Project

A business card with all contact details with logo design on there (already have a logo) eye catching Logo and contact info on one side, full logo on the back, must target upper class residential and corporate companies, fitness companies, still keep it on the feminine side of things , must look elegant

Target Market(s)

Upper class homes and corporate companies

Industry/Entity Type

Cleaning Service

Contact Information for Business Card

Name: Marisol Quenby
Position: Director
ABN: 31647209853
Email: marisolssilvercleaning@tidymail.example
Number: 0417906354

Font styles to use
Decorative

Colors

Designer to choose colors to be used in the design.

Requirements
Must have
• Available Sydney Wide, contact info and logo on one side, full logo on the back
Nice to have
• Professional appearance
Should not have
• Cheap advert looking stuff

```html
<!DOCTYPE html>
<html lang="en">
<head>
<meta charset="UTF-8">
<title>Silver Bloom – Business Cards</title>
<link href="https://fonts.googleapis.com/css2?family=Marcellus&family=Lato:wght@400&display=swap" rel="stylesheet">
<style>
  :root {
    --backdrop: #3a322d;
    --card: #0d0d0d;
    --teal: #33e3d3;
    --teal-soft: rgba(51, 227, 211, .28);
    --silver: #d4d4d4;
    --silver-soft: rgba(212, 212, 212, .25);
    --ink: #f2f2f2;
    --rule: #3a3a3a;
  }
  * { margin: 0; padding: 0; box-sizing: border-box; }
  html, body { width: 1200px; height: 900px; overflow: hidden; }
  body {
    background: var(--backdrop);
    font-family: "Lato", Arial, sans-serif;
    position: relative;
  }
  .card {
    position: absolute;
    top: 290px;
    width: 540px;
    height: 310px;
    background: var(--card);
    border-radius: 3px;
    box-shadow: 0 10px 28px rgba(0,0,0,.45);
  }
  .card--front { left: 45px; }
  .card--back { left: 615px; }

  .brand {
    position: absolute;
    display: flex;
    flex-direction: column;
    align-items: center;
    font-family: "Marcellus", Georgia, serif;
    font-weight: 400;
    text-align: center;
    text-transform: uppercase;
    line-height: 1.15;
  }
  .brand__mark { border: 2px solid currentColor; }
  .brand__ornament { border-radius: 50%; }
  .brand__name { display: block; }
  .brand__tagline { display: block; letter-spacing: .22em; }

  .card--front .brand {
    color: var(--teal);
    top: 24px;
    right: 40px;
    width: 260px;
  }
  .card--front .brand__mark { width: 46px; height: 46px; }
  .card--front .brand__ornament {
    width: 220px; height: 22px; margin-top: 6px;
    background: radial-gradient(ellipse at center, var(--teal-soft), transparent 70%);
  }
  .card--front .brand__name { font-size: 28px; letter-spacing: .04em; margin-top: 4px; }
  .card--front .brand__tagline { font-size: 8.5px; margin-top: 4px; color: var(--silver); }

  .divider {
    position: absolute;
    left: 230px;
    right: 30px;
    top: 176px;
    height: 1px;
    background: var(--rule);
  }
  .abn {
    position: absolute;
    right: 34px;
    top: 190px;
    font-size: 14px;
    color: var(--ink);
  }
  .abn__label { color: var(--teal); margin-right: 4px; }

  .contact {
    position: absolute;
    left: 30px;
    bottom: 24px;
    width: 320px;
  }
  .contact__name {
    font-family: "Marcellus", Georgia, serif;
    font-weight: 400;
    color: var(--teal);
    font-size: 21px;
    letter-spacing: .06em;
    text-transform: uppercase;
    display: flex;
    align-items: center;
    gap: 12px;
  }
  .contact__name::after {
    content: "";
    flex: 1;
    height: 1px;
    background: var(--rule);
  }
  .contact__role {
    color: var(--ink);
    font-size: 14px;
    margin: 2px 0 10px;
  }
  .contact__line {
    display: flex;
    align-items: center;
    gap: 7px;
    color: var(--ink);
    font-size: 14px;
    margin-top: 4px;
    white-space: nowrap;
  }
  .contact__line svg { width: 13px; height: 13px; flex: none; }

  .card--back .brand {
    color: var(--silver);
    left: 0;
    right: 0;
    top: 46px;
  }
  .card--back .brand__mark { width: 78px; height: 78px; }
  .card--back .brand__ornament {
    width: 280px; height: 30px; margin-top: 8px;
    background: radial-gradient(ellipse at center, var(--silver-soft), transparent 70%);
  }
  .card--back .brand__name { font-size: 36px; letter-spacing: .05em; margin-top: 8px; }
  .card--back .brand__tagline { font-size: 10px; margin-top: 6px; }
</style>
</head>
<body>
  <section class="card card--front" aria-label="Business card front">
    <div class="brand">
      <span class="brand__mark" aria-hidden="true"></span>
      <span class="brand__ornament" role="img" aria-label="Floral swirl ornament"></span>
      <span class="brand__name">Silver Bloom</span>
      <span class="brand__tagline">Marisol's Cleaning Service</span>
    </div>
    <div class="divider"></div>
    <p class="abn"><span class="abn__label">ABN:</span>31647209853</p>
    <div class="contact">
      <h1 class="contact__name">Marisol Quenby</h1>
      <p class="contact__role">Director</p>
      <p class="contact__line">
        <svg viewBox="0 0 16 16" aria-hidden="true"><path fill="var(--teal)" d="M3.6 1.5l2.3 2.6-1.3 1.8c.9 2 2.4 3.5 4.4 4.4l1.8-1.3 2.6 2.3-1.4 2.2C7 15 1 9 1.4 2.9z"/></svg>
        0417906354
      </p>
      <p class="contact__line">
        <svg viewBox="0 0 16 16" aria-hidden="true"><rect x="1" y="3" width="14" height="10" fill="var(--teal)"/><path d="M1 3l7 6 7-6" fill="none" stroke="var(--card)" stroke-width="1.3"/></svg>
        marisolssilvercleaning@tidymail.example
      </p>
    </div>
  </section>

  <section class="card card--back" aria-label="Business card back">
    <div class="brand">
      <span class="brand__mark" aria-hidden="true"></span>
      <span class="brand__ornament" role="img" aria-label="Floral swirl ornament"></span>
      <span class="brand__name">Silver Bloom</span>
      <span class="brand__tagline">Marisol's Cleaning Service</span>
    </div>
  </section>
</body>
</html>
```